Strategy and Technology Consulting - Our Story and Values Page

Interior Page design – Our History and Our Values

Our homepage has been designed and we are looking for a design for one of the interior pages. This interior page tells the story of Our History and Our Values

Because the homepage has been designed, we would like this interior page to reflect the design of the homepage without being a mirror image of the homepage.

This site will be implemented in WordPress using the Elementor framework.

Font: Poppins medium and Poppins dark
Illustrations: Our homepage illustrations were designed by “Brelin 1974” on Quillmark. Compatible original or stock illustrations are welcome. Stock photography is also welcome. Brelin is also available through Brelin Tosamek on Ravolo

Uploaded Files
• Homepage design – this is the design we will use for our homepage. Contest entries should reflect this basic style but should be distinctly different from the homepage.
• Our History and Our Values – Wireframe – the basic layout of the page we are looking for.
• Our History and Our Values – Word document with the text supporting the wireframe.
• Color Palette – please use colors compatible with the palette attached.

Our Story - timeline
There is a timeline element in the wireframe. The wireframe displays this as a series of chevrons (arrows), but it does not need to be. Creativity in display of the timeline is appreciated.

Our Values
If you look at the Word document, you will see that there are a lot of words on the page. The winning design will present the information in a way that engages the user without overwhelming them with too much to read. For example, they may click on a value and see more information.

Target Market(s)

CIO's and Technology Executives

Number of Pages Required

1 page

Font styles to use
Sans Serif
Other font styles liked:
• Poppin

Requirements
Must have
• A timeline element, all of our values
Nice to have
• Clever timeline display

```html
<!DOCTYPE html>
<html lang="en">
<head>
<meta charset="utf-8">
<title>Veltrana – Our Story and Values</title>
<link href="https://fonts.googleapis.com/css2?family=Poppins:wght@400;500;600;700;800&display=swap" rel="stylesheet">
<style>
:root{
  --navy:#2a5379;
  --navy-dark:#2c5577;
  --blue:#1a6fb8;
  --blue-light:#c9def0;
  --orange:#f0a914;
  --orange-2:#f7a81b;
  --cyan:#adf4f5;
  --teal:#9dd0d4;
  --ink:#2c3e50;
  --grey:#5b6670;
  --white:#ffffff;
  --footer-bar:#25435e;
}
*{margin:0;padding:0;box-sizing:border-box}
html,body{width:1200px;height:3292px;overflow:hidden}
body{font-family:"Poppins",sans-serif;background:var(--white);position:relative;color:var(--ink)}
.abs{position:absolute}

/* header */
.site-header{position:absolute;left:0;top:0;width:1200px;height:90px;border-bottom:1px solid #eef1f4;background:var(--white);z-index:5}
.brand{position:absolute;left:92px;top:18px;font-size:46px;font-weight:500;color:#9fb6c8;letter-spacing:0.5px;display:flex;align-items:center;gap:8px}
.brand-dot{width:12px;height:12px;background:var(--blue);display:inline-block}
.main-nav{position:absolute;left:543px;top:35px;display:flex;gap:22px;align-items:center;font-size:13px;font-weight:600;color:var(--navy)}
.main-nav span::after{content:" ⌄";font-size:11px}
.main-nav .home{width:14px;height:14px}
.btn{display:inline-flex;align-items:center;justify-content:center;background:var(--orange);color:var(--white);font-weight:700;font-size:12px;border-radius:22px;text-transform:uppercase}
.header-cta{position:absolute;left:979px;top:26px;width:130px;height:37px}

/* story */
.section-title{position:absolute;width:1200px;text-align:center;font-weight:700;letter-spacing:0.5px}
.story-title{top:148px;font-size:36px;color:var(--navy)}
.era{position:absolute;top:234px;width:298px;height:354px;border:3px solid;border-radius:30px}
.era-card{position:absolute;left:16px;top:20px;width:261px;height:310px;background:var(--white);border-radius:26px;box-shadow:0 10px 24px rgba(30,60,90,.12)}
.era-tab{position:absolute;left:-17px;top:40px;width:226px;height:48px;border-radius:0 14px 14px 14px;color:var(--white);font-weight:600;font-size:20px;display:flex;align-items:center;justify-content:center}
.era ul{list-style:none;position:absolute;left:38px;top:96px;width:220px;font-size:14.5px;line-height:32.5px;color:var(--ink)}
.era li{position:relative;padding-left:0}
.era li.dot::before{content:"";position:absolute;left:-25px;top:12px;width:10px;height:10px;border-radius:50%;background:currentColor}
.era li.sub{padding-left:14px}
.era-1{left:114px;border-color:var(--blue)} .era-1 .era-tab{background:var(--blue)} .era-1 li.dot::before{background:var(--blue)}
.era-2{left:457px;border-color:var(--orange)} .era-2 .era-tab{background:var(--orange)} .era-2 li.dot::before{background:var(--orange)}
.era-3{left:801px;border-color:var(--navy-dark)} .era-3 .era-tab{background:var(--navy-dark)} .era-3 li.dot::before{background:var(--navy-dark)}

/* values */
.values-title{top:990px;font-size:44px;color:var(--white)}
.value{position:absolute;left:98px;width:1004px;height:174px;background:var(--white)}
.value-art{position:absolute;left:15px;top:15px;width:192px;height:145px}
.value h3{position:absolute;left:234px;top:20px;font-size:19px;font-weight:500;color:var(--navy)}
.value p{position:absolute;left:234px;top:52px;width:730px;font-size:14.6px;line-height:31px;color:var(--grey)}

/* newsletter */
.newsletter{position:absolute;left:128px;top:2575px;width:934px;height:209px;border-radius:105px;background:linear-gradient(90deg,var(--orange-2),#f4a31a)}
.newsletter h2{position:absolute;left:82px;top:58px;font-size:33px;font-weight:800;color:var(--white)}
.newsletter p{position:absolute;left:82px;top:110px;font-size:16px;line-height:20px;font-weight:500;color:var(--white);width:430px}
.email-field{position:absolute;left:556px;top:83px;width:323px;height:46px;border-radius:23px;background:var(--white);display:flex;align-items:center;padding-left:46px;font-size:13px;color:#8a98a5}
.send{position:absolute;right:4px;top:4px;width:38px;height:38px;border-radius:50%;background:var(--teal);display:flex;align-items:center;justify-content:center}

/* footer */
.footer-brand{position:absolute;left:109px;top:2965px;font-size:66px;font-weight:500;color:#c7d5e0;display:flex;align-items:center;gap:10px}
.socials{position:absolute;left:167px;top:3044px;display:flex;gap:9px}
.socials span{width:42px;height:42px;border-radius:50%;background:rgba(255,255,255,.25)}
.footer-cta{position:absolute;left:206px;top:3109px;width:133px;height:40px}
.f-col{position:absolute;top:2940px;color:var(--white)}
.f-col h4{font-size:19px;font-weight:700;margin-bottom:20px}
.f-col li{list-style:none;font-size:13px;line-height:31.6px}
.f-col li::before{content:"›  "}
.contact-item{display:flex;gap:10px;font-size:13px;line-height:17px;margin-bottom:21px}
.contact-item svg{flex:none;margin-top:2px}
.bottom-bar{position:absolute;left:0;top:3236px;width:1200px;height:56px;background:var(--footer-bar);color:var(--white);font-size:13px;font-weight:500;text-align:center;line-height:56px}
.chat{position:absolute;left:1136px;top:3185px;width:48px;height:48px;border-radius:50%;background:var(--orange);display:flex;align-items:center;justify-content:center}
</style>
</head>
<body>

<!-- backgrounds -->
<svg class="abs" style="left:0;top:0" width="1200" height="3292" viewBox="0 0 1200 3292" aria-hidden="true">
  <defs>
    <linearGradient id="footGrad" x1="0" y1="1" x2="1" y2="0">
      <stop offset="0" stop-color="#4d87a6"/>
      <stop offset="0.6" stop-color="#2f5a7c"/>
      <stop offset="1" stop-color="#2c5577"/>
    </linearGradient>
    <linearGradient id="blueGrad" x1="0" y1="0" x2="1" y2="1">
      <stop offset="0" stop-color="#1c72bb"/>
      <stop offset="1" stop-color="#1767ad"/>
    </linearGradient>
  </defs>
  <path d="M0 740 C150 846 300 916 480 866 C650 816 760 666 920 670 C1040 674 1120 736 1200 791" fill="none" stroke="var(--blue-light)" stroke-width="16"/>
  <path d="M0 754 C150 860 300 930 480 880 C650 830 760 680 920 684 C1040 688 1120 750 1200 805 L1200 2482 L0 2482Z" fill="url(#blueGrad)"/>
  <path d="M0 2605 C200 2700 300 2860 420 2855 C520 2850 560 2790 640 2800 C760 2815 800 2870 900 2850 C1000 2830 1100 2620 1200 2600" fill="none" stroke="#cfe3ea" stroke-width="14" transform="translate(0,10)"/>
  <path d="M0 2605 C200 2700 300 2860 420 2855 C520 2850 560 2790 640 2800 C760 2815 800 2870 900 2850 C1000 2830 1100 2620 1200 2600 L1200 3292 L0 3292Z" fill="url(#footGrad)"/>
</svg>

<header class="site-header">
  <div class="brand"><span class="brand-dot"></span>Veltrana</div>
  <nav class="main-nav">
    <svg class="home" viewBox="0 0 14 14"><path d="M7 1 L13 6.5 H11 V13 H8.5 V9 H5.5 V13 H3 V6.5 H1Z" fill="#9fb6c8"/></svg>
    <span>About Us</span><span>Services</span><span>Insights</span><span>Join Us</span>
  </nav>
  <a class="btn header-cta">Contact Us</a>
</header>

<h2 class="section-title story-title">OUR STORY</h2>

<div class="era era-1">
  <div class="era-card">
    <div class="era-tab">2017 – 2019</div>
    <ul>
      <li class="dot">Growth Strategy Focus</li>
      <li class="dot">Consistent, Modest Growth</li>
      <li class="dot">Preliminary Focus on</li>
      <li>Technology</li>
      <li class="dot"><b style="font-weight:600">Eureka!</b> Implementing</li>
      <li>strategy is hard.</li>
    </ul>
  </div>
</div>
<div class="era era-2">
  <div class="era-card">
    <div class="era-tab">2020 – 2021</div>
    <ul>
      <li class="dot">Pandemic Pauses Growth</li>
      <li class="dot">Rethinking :</li>
      <li class="sub">-&nbsp; the business model</li>
      <li class="sub">-&nbsp; the delivery model</li>
    </ul>
  </div>
</div>
<div class="era era-3">
  <div class="era-card">
    <div class="era-tab">2022 and Onward</div>
    <ul>
      <li class="dot">Leadership Team for Focus</li>
      <li>on Essential Areas</li>
      <li class="dot">Rapid Growth</li>
      <li class="dot">Customer Success</li>
    </ul>
  </div>
</div>

<h2 class="section-title values-title">OUR VALUES</h2>

<article class="value" style="top:1061px">
  <div class="value-art" style="background:var(--orange)" role="img" aria-label="Line icon of hands holding a person beneath stars"></div>
  <h3>The Value of Every Human.&nbsp; Regardless.</h3>
  <p>Each person's unique experiences and perspectives add vibrant hues to the tapestry of our shared existence.&nbsp; In a world where diversity paints the canvas of humanity, true beauty is found in recognizing the inherent and incalculable value of every human being.</p>
</article>
<article class="value" style="top:1255px">
  <div class="value-art" style="background:var(--cyan)" role="img" aria-label="Line icon of people connected in a cycle"></div>
  <h3>Collaboration</h3>
  <p>Collaboration in work transforms individual endeavors into symphonies of collective achievement. Through collaboration, diverse talents converge, fostering a rich exchange of ideas that amplifies creativity, accelerates progress, and brings forth solutions beyond what a single mind could conceive.</p>
</article>
<article class="value" style="top:1449px">
  <div class="value-art" style="background:var(--teal)" role="img" aria-label="Line icon of a raised fist with a check mark"></div>
  <h3>Passion</h3>
  <p>Passion infuses our work with energy, transforming routine tasks into opportunities for creativity and innovation. Fueled by passion, individuals become unstoppable forces, driven to overcome challenges and achieve remarkable outcomes that benefit them and inspire those around them</p>
</article>
<article class="value" style="top:1643px">
  <div class="value-art" style="background:var(--navy-dark)" role="img" aria-label="Line icon of a hand holding an award medal"></div>
  <h3>Excellence</h3>
  <p>Excellence isn't a destination; it's a continuous journey of refinement and growth. Striving for excellence cultivates a culture of continuous improvement, fostering innovation, credibility, and a lasting impact that resonates far beyond the immediate task.</p>
</article>
<article class="value" style="top:1837px">
  <div class="value-art" style="background:var(--orange-2)" role="img" aria-label="Line icon of a person climbing bar chart steps toward a gear"></div>
  <h3>Tenacity</h3>
  <p>Tenacity is the unwavering anchor that keeps us grounded amidst adversity, propelling us forward when faced with obstacles. The resilience to persist, adapt, and learn from setbacks leads to the mastery of skills and the fulfillment of ambitious goals.</p>
</article>
<article class="value" style="top:2031px">
  <div class="value-art" style="background:var(--cyan)" role="img" aria-label="Line icon of a person with a thinking mind"></div>
  <h3>Solution Mindset</h3>
  <p>A solution mindset is the compass that directs our focus from problems to possibilities. It empowers us to navigate challenges with a proactive mindset, igniting a journey of exploration and innovation that not only resolves issues but also paves the way for continuous growth and success.</p>
</article>
<article class="value" style="top:2225px">
  <div class="value-art" style="background:var(--teal)" role="img" aria-label="Line icon of two colleagues sitting together"></div>
  <h3>Generosity</h3>
  <p>Generosity creates a virtuous cycle of goodwill, fostering a sense of unity and shared purpose among colleagues. By freely sharing knowledge, support, and resources, we uplift those around us and contribute to a collaborative environment where collective achievements flourish.</p>
</article>

<section class="newsletter">
  <h2>Subscribe Our Newsletter</h2>
  <p>Subscribe our newsletter to receive the latest news and exclusive offers every week, No spam.</p>
  <div class="email-field">
    <svg class="abs" style="left:22px;top:17px" width="14" height="11" viewBox="0 0 14 11"><rect width="14" height="11" rx="1.5" fill="#9aa9b6"/><path d="M1 1.5 L7 6 L13 1.5" stroke="#fff" stroke-width="1.3" fill="none"/></svg>
    Enter email address
    <span class="send"><svg width="16" height="16" viewBox="0 0 16 16"><path d="M1 8 L15 1 L11 15 L8 9Z" fill="#fff"/></svg></span>
  </div>
</section>

<div class="footer-brand"><span class="brand-dot" style="width:14px;height:14px"></span>Veltrana</div>
<div class="socials" aria-label="Social links"><span></span><span></span><span></span><span></span></div>
<a class="btn footer-cta">Contact Us</a>

<div class="f-col" style="left:486px">
  <h4>Quick links</h4>
  <ul><li>Home</li><li>About Us</li><li>Services</li><li>Insights</li><li>Join Us</li><li>Contact Us</li></ul>
</div>
<div class="f-col" style="left:665px">
  <h4>Our Services</h4>
  <ul><li>Business Transformation</li><li>ERP Implementations</li><li>ERP Solutions</li><li>BI and Data</li><li>Building the Right Team...</li></ul>
</div>
<div class="f-col" style="left:898px">
  <h4>Contact info</h4>
  <div class="contact-item"><svg width="13" height="10" viewBox="0 0 13 10"><rect width="13" height="10" rx="1" fill="var(--orange)"/><path d="M1 1 L6.5 5 L12 1" stroke="#2c5577" fill="none"/></svg><div>Email:<br>hello@veltrana.com</div></div>
  <div class="contact-item"><svg width="13" height="13" viewBox="0 0 13 13"><path d="M2 1 L5 1 L6 4 L4.5 5.5 C5.5 7.5 6 8 7.5 8.5 L9 7 L12 8 L12 11 C6 12 1 7 2 1Z" fill="var(--orange)"/></svg><div>Phone:<br>+44 100 200 3000</div></div>
  <div class="contact-item"><svg width="12" height="15" viewBox="0 0 12 15"><path d="M6 0 C2.7 0 0 2.6 0 5.8 C0 10 6 15 6 15 C6 15 12 10 12 5.8 C12 2.6 9.3 0 6 0Z" fill="var(--orange)"/><circle cx="6" cy="5.8" r="2.2" fill="#2c5577"/></svg><div>Location:<br>Some address line goes<br>here city name</div></div>
</div>

<footer class="bottom-bar">© Veltrana Design 2023, All Rights Reserved</footer>
<div class="chat"><svg width="24" height="20" viewBox="0 0 24 20"><path d="M3 2 H21 V14 H9 L4 18 V14 H3Z" fill="#fff"/><circle cx="8" cy="8" r="1.4" fill="var(--orange)"/><circle cx="12" cy="8" r="1.4" fill="var(--orange)"/><circle cx="16" cy="8" r="1.4" fill="var(--orange)"/></svg></div>

</body>
</html>
```